Vorelan.com Personal Trainer/Fitness Website

I want a website to market my personal training/Outdoor Bootcamp Class services, as well as to ditribute nutrivex. I need a logo as well I included an address for the Harbor Gales 1975 logo. I'd like Vorelan in place of Harbor Gales, and in Black and white, just different enough so I can't get sued by the PBL.
https://www.pictofind.example/imgres?imgurl=http%3A%2F%2Fwww.darnell-quibury.example%2Fwp-content%2Fuploads%2F2014%2F01%2Fgales_logo4.jpg&imgrefurl=http%3A%2F%2Fwww.darnell-quibury.example%2Fpbl-logo-redesigns-harbor-gales%2F&docid=_qkwzR7TBAgXpL&tbnid=m4tpU8KdOXjnRP%3A&w=600&h=450&client=ms-android-carrier&bih=512&biw=360&ved=0ahUKEwiRtpgyp9HMAhUTwGMKHRPMBWMQMwg6KBQwFA&iact=mrc&uact=8.
It should be about 5 pages 1. home 2. about 3. Services 4. Blog/Videos and programs 5. Contact.
http://www.dorvinfitness.example.uk/ is a website I like the style of.

Target Market(s)

Seattle area

Industry/Entity Type

Fitness

Coding

Coded - Design and coding required

Number of Pages Required

4 page

Font styles to use
Serif
Sans Serif

Requirements
Must have
• A minimal look
Nice to have
• A logo similar to the 1975 Harbor Galewinds Logo, with a Small Milo Brandt ripping his shirt open(with a picture of the logo on his shirt, picture within picture) to turn into Ironjaw in the center. Skyline is black, Background and small figure white(with black logo on shirt)

```html
<!DOCTYPE html>
<html lang="en">
<head>
<meta charset="utf-8">
<title>Vorelan — Personal Training &amp; Outdoor Bootcamp</title>
<link rel="stylesheet" href="https://fonts.googleapis.com/css2?family=Open+Sans:wght@300;400;600;700&display=swap">
<style>
:root{
  --ink:#111111;
  --black:#000000;
  --coal:#1c1c1c;
  --slate:#2a2a2a;
  --steel:#3b3b3b;
  --mist:#8d8d8d;
  --paper:#ffffff;
  --fog:#e9e9e9;
  --text:#555555;
}
*{box-sizing:border-box;margin:0;padding:0}
html,body{width:1200px;height:3460px;overflow:hidden}
body{font-family:"Open Sans",Arial,sans-serif;color:var(--text);background:var(--paper);position:relative}
section,header,nav,footer{position:absolute;left:0;width:1200px}
.btn{display:inline-block;background:var(--ink);color:var(--paper);font-weight:600;text-transform:uppercase;border-radius:14px;letter-spacing:.5px}
.heading{font-weight:300;text-transform:uppercase;letter-spacing:2px;text-align:center}
.heading strong{font-weight:700}
.rule{width:60px;height:2px;background:currentColor;margin:14px auto 0}
.arrow{position:absolute;top:50%;width:30px;height:50px;margin-top:-25px}

/* header */
.site-header{top:0;height:128px;background:var(--paper)}
.brand{position:absolute;left:76px;top:26px;display:flex;align-items:center;gap:14px}
.brand-mark{width:26px;height:26px;background:var(--ink)}
.brand-name{font-size:42px;font-weight:700;color:var(--ink);letter-spacing:1px}
.join{position:absolute;right:80px;top:20px;padding:12px 34px;font-size:22px;text-transform:none;border-radius:4px}
.contact-strip{position:absolute;right:80px;top:82px;display:flex;align-items:center;gap:12px;font-weight:700;color:var(--ink);font-size:22px}
.dot{width:28px;height:28px;border-radius:50%;background:var(--ink)}
.dot.soft{background:var(--steel)}

/* nav */
.main-nav{top:128px;height:52px;background:var(--coal);z-index:2}
.main-nav ul{list-style:none;display:flex;margin-left:80px;height:52px}
.main-nav li{width:148px;color:var(--paper);font-size:15px;font-weight:600;display:flex;align-items:center;justify-content:center}
.main-nav li.active{background:var(--steel)}

/* hero */
.hero{top:180px;height:620px;overflow:hidden;background:linear-gradient(180deg,#9bb7c6 0%,#7f9a8a 45%,#5f8a3e 75%,#4d7a30 100%)}
.hero-circle{position:absolute;left:384px;top:-60px;width:432px;height:432px;border-radius:50%;background:rgba(40,40,40,.55);text-align:center;color:var(--paper);padding-top:240px}
.hero-circle h1{font-weight:300;font-size:30px;line-height:38px;letter-spacing:1px}
.hero-circle .btn{margin-top:18px;padding:8px 22px;font-size:15px;border:2px solid var(--paper)}

/* welcome */
.welcome{top:800px;height:220px;text-align:center;background:var(--paper)}
.welcome-mark{width:52px;height:52px;border-radius:50%;background:var(--ink);margin:18px auto 6px}
.welcome h2{font-size:30px;color:var(--ink)}
.welcome p{width:1060px;margin:12px auto 0;font-size:12px;line-height:18px}
.welcome .btn{margin-top:14px;padding:5px 16px;font-size:11px}

/* services */
.services{top:1020px;height:440px;background:linear-gradient(180deg,#d3d3d3,#bdbdbd);color:var(--ink)}
.services .heading{margin-top:52px;font-size:30px}
.services .sub{text-align:center;font-size:14px;margin-top:28px;letter-spacing:1px}
.service-list{display:flex;justify-content:space-between;width:1000px;margin:40px auto 0}
.service{width:200px;text-align:center;font-weight:700;font-size:14px;text-transform:uppercase}
.service-icon{width:110px;height:110px;border-radius:50%;background:var(--ink);border:4px solid var(--paper);margin:0 auto 28px;display:flex;align-items:center;justify-content:center}

/* gallery */
.gallery{top:1460px;height:500px;background:var(--slate);color:var(--paper)}
.gallery .heading{margin-top:52px;font-size:30px}
.tile{position:absolute}
.play{position:absolute;left:50%;top:50%;width:50px;height:36px;margin:-18px 0 0 -25px;background:var(--ink);border-radius:8px}

/* events */
.events{top:1960px;height:550px;background:linear-gradient(180deg,#8a8a8a,#6f6f6f);color:var(--paper)}
.events .heading{margin-top:110px;font-size:30px}
.events .sub{text-align:center;font-size:13px;margin-top:16px;letter-spacing:1px}
.card{position:absolute;top:188px;width:300px;height:300px;background:var(--paper);text-align:center;color:var(--text)}
.card-photo{height:152px}
.date{position:absolute;left:14px;top:0;width:54px;height:60px;background:var(--ink);color:var(--paper);font-weight:700;font-size:22px;line-height:26px;padding-top:6px}
.date small{display:block;font-size:11px;font-weight:400}
.card h3{font-size:15px;color:var(--ink);margin-top:12px}
.card p{font-size:12px;line-height:17px;padding:6px 22px 0}
.card .btn{margin-top:10px;padding:4px 16px;font-size:11px}

/* testimonials */
.testimonials{top:2510px;height:470px;background:var(--black);color:var(--paper)}
.testimonials .heading{margin-top:64px;font-size:30px}
.quote{position:absolute;left:160px;top:162px;width:880px;height:156px;background:var(--steel);border-radius:10px;padding:28px 34px 0 70px;font-size:13px;line-height:20px;color:#dcdcdc}
.quote-mark{position:absolute;left:26px;top:18px;font-size:48px;font-weight:700;color:var(--mist);line-height:48px}
.quote::after{content:"";position:absolute;left:60px;bottom:-18px;border:18px solid transparent;border-top-color:var(--steel);border-bottom:0}
.author{position:absolute;left:300px;top:350px;font-weight:700;font-size:20px;letter-spacing:1px}

/* footer */
.site-footer{top:2980px;height:480px;background:var(--coal);color:#cfcfcf}
.newsletter{position:absolute;left:80px;top:40px;display:flex;align-items:center;gap:20px;width:1040px}
.label{font-weight:700;color:var(--paper);font-size:16px;letter-spacing:1px}
.field{background:var(--paper);color:#999;font-size:12px;padding:0 10px;display:flex;align-items:center}
.subscribe{background:var(--ink);color:var(--paper);font-size:12px;font-weight:700;width:100px;height:38px;display:flex;align-items:center;justify-content:center}
.follow{margin-left:auto;display:flex;align-items:center;gap:12px}
.footer-rule{position:absolute;left:80px;top:112px;width:1040px;height:1px;background:#444}
.col{position:absolute;top:150px}
.col h4{font-size:16px;color:var(--paper);letter-spacing:1px;display:flex;align-items:center;gap:10px;margin-bottom:20px}
.col h4 span{width:18px;height:18px;border-radius:50%;border:2px solid var(--paper)}
.inquiry{left:80px;width:520px;height:200px}
.inquiry .field{position:absolute;height:34px;width:220px}
.links ul{list-style:none;font-size:12px;line-height:24px;text-transform:uppercase}
.links li::before{content:"› ";color:var(--mist)}
.details p{font-size:14px;margin-bottom:14px;display:flex;align-items:center;gap:10px}
.details .brand-name{font-size:30px;color:var(--paper)}
.copyright{position:absolute;left:0;bottom:0;width:1200px;height:52px;background:var(--black);text-align:center;line-height:52px;font-size:12px;letter-spacing:1px}
</style>
</head>
<body>

<header class="site-header">
  <div class="brand"><span class="brand-mark"></span><span class="brand-name">VORELAN</span></div>
  <span class="btn join">Join A Session</span>
  <div class="contact-strip">
    <svg width="26" height="26" viewBox="0 0 24 24"><path d="M6.6 10.8a15 15 0 0 0 6.6 6.6l2.2-2.2c.3-.3.7-.4 1-.2 1.1.4 2.300.6 3.6.6.6 0 1 .4 1 1V20c0 .6-.4 1-1 1A17 17 0 0 1 3 4c0-.6.4-1 1-1h3.5c.6 0 1 .4 1 1 0 1.3.2 2.5.6 3.6.1.3 0 .7-.2 1z" fill="#111"/></svg>
    <span>206-555-0148</span>
    <span class="dot"></span><span class="dot soft"></span>
  </div>
</header>

<nav class="main-nav">
  <ul>
    <li class="active">HOME</li><li>ABOUT</li><li>SERVICES</li><li>BLOG</li><li>VIDEOS</li><li>PROGRAMS</li><li>CONTACT</li>
  </ul>
</nav>

<section class="hero" role="img" aria-label="Photo of a group of people doing partner sit-ups on a park lawn">
  <div class="hero-circle">
    <h1>GET FIT AND HAVE FUN<br>THE WAY IT SHOULD BE</h1>
    <span class="btn">Contact Us</span>
  </div>
</section>

<section class="welcome">
  <div class="welcome-mark"></div>
  <h2 class="heading">Welcome to <strong>Vorelan</strong></h2>
  <p>Train with a coach who plans every session around your goals, your schedule and your pace. We run personal training, outdoor bootcamp classes and group sessions across the city, with online coaching for days you cannot make it in person. Every program mixes strength, cardio and mobility work, tracks your progress week by week, and adds simple nutrition support so results last long after the workout ends.</p>
  <span class="btn">Read More</span>
</section>

<section class="services">
  <h2 class="heading">Our <strong>Services</strong><div class="rule"></div></h2>
  <p class="sub">SELECT TO LEARN MORE</p>
  <div class="service-list">
    <div class="service">
      <div class="service-icon"><svg width="54" height="54" viewBox="0 0 54 54" fill="#fff"><rect x="4" y="18" width="8" height="18"/><rect x="12" y="14" width="6" height="26"/><rect x="18" y="25" width="18" height="4"/><rect x="36" y="14" width="6" height="26"/><rect x="42" y="18" width="8" height="18"/></svg></div>
      Personal Training
    </div>
    <div class="service">
      <div class="service-icon"><svg width="54" height="54" viewBox="0 0 54 54" fill="none" stroke="#fff" stroke-width="4"><circle cx="27" cy="30" r="17"/><path d="M27 30V20M22 8h10M27 8v5"/></svg></div>
      Outdoor Bootcamp Classes
    </div>
    <div class="service">
      <div class="service-icon"><svg width="54" height="54" viewBox="0 0 54 54" fill="#fff"><rect x="12" y="8" width="4" height="40"/><path d="M16 10h26l-6 8 6 8H16z"/></svg></div>
      Outdoor Group Training
    </div>
    <div class="service">
      <div class="service-icon"><svg width="54" height="54" viewBox="0 0 54 54" fill="none" stroke="#fff" stroke-width="4"><rect x="6" y="10" width="42" height="28" rx="2"/><path d="M20 46h14M27 38v8"/></svg></div>
      Online Coaching
    </div>
  </div>
</section>

<section class="gallery">
  <h2 class="heading">Our <strong>Gallery</strong><div class="rule"></div></h2>
  <svg class="arrow" style="left:22px" viewBox="0 0 30 50"><path d="M24 4L6 25l18 21" fill="none" stroke="#fff" stroke-width="4"/></svg>
  <svg class="arrow" style="right:22px" viewBox="0 0 30 50"><path d="M6 4l18 21L6 46" fill="none" stroke="#fff" stroke-width="4"/></svg>
  <div class="tile" style="left:80px;top:140px;width:310px;height:348px;background:linear-gradient(160deg,#9a8f86,#4d4a47)" role="img" aria-label="Video of an indoor workout session"><span class="play"></span><svg class="play" style="background:none" viewBox="0 0 50 36"><path d="M20 10l12 8-12 8z" fill="#fff"/></svg></div>
  <div class="tile" style="left:400px;top:140px;width:200px;height:126px;background:linear-gradient(160deg,#c9c4bd,#7c776f)" role="img" aria-label="Photo of people training indoors"></div>
  <div class="tile" style="left:608px;top:140px;width:290px;height:126px;background:linear-gradient(160deg,#b7b0a8,#5f5a55)" role="img" aria-label="Photo of a class using exercise balls"></div>
  <div class="tile" style="left:400px;top:274px;width:124px;height:214px;background:linear-gradient(160deg,#a9c18a,#4f6e33)" role="img" aria-label="Photo of an outdoor bootcamp"></div>
  <div class="tile" style="left:532px;top:274px;width:200px;height:214px;background:linear-gradient(160deg,#d8c2c0,#8b4a4f)" role="img" aria-label="Photo of a woman training with a kettlebell"></div>
  <div class="tile" style="left:740px;top:274px;width:158px;height:214px;background:linear-gradient(160deg,#bdb6ae,#55504c)" role="img" aria-label="Photo of a gym session"></div>
  <div class="tile" style="left:906px;top:140px;width:214px;height:348px;background:linear-gradient(160deg,#c8bfb5,#5a514b)" role="img" aria-label="Photo of a man lifting weights"></div>
</section>

<section class="events">
  <h2 class="heading">Upcoming <strong>Events</strong><div class="rule"></div></h2>
  <p class="sub">JOIN US FOR AN EVENT!</p>
  <svg class="arrow" style="left:22px" viewBox="0 0 30 50"><path d="M24 4L6 25l18 21" fill="none" stroke="#fff" stroke-width="4"/></svg>
  <svg class="arrow" style="right:22px" viewBox="0 0 30 50"><path d="M6 4l18 21L6 46" fill="none" stroke="#fff" stroke-width="4"/></svg>
  <div class="card" style="left:114px">
    <div class="card-photo" role="img" aria-label="Photo of an outdoor group class on a field" style="background:linear-gradient(180deg,#b9d3e6,#6d9a4b)"></div>
    <div class="date">12<small>MAY</small></div>
    <h3>LOREM IPSUM DOLOR SIT AMET</h3>
    <p>Morning bootcamp in the park with circuits, sprints and partner drills for every level.</p>
    <span class="btn">Read More</span>
  </div>
  <div class="card" style="left:450px">
    <div class="card-photo" role="img" aria-label="Photo of a crowded indoor fitness class" style="background:linear-gradient(180deg,#e0d8cf,#8c8178)"></div>
    <div class="date">11<small>JUN</small></div>
    <h3>LOREM IPSUM DOLOR SIT AMET</h3>
    <p>Strength workshop covering squat, hinge and press technique with small group coaching.</p>
    <span class="btn">Read More</span>
  </div>
  <div class="card" style="left:786px">
    <div class="card-photo" role="img" aria-label="Photo of two people doing a partner workout" style="background:linear-gradient(180deg,#cfd6dc,#6b7a86)"></div>
    <div class="date">09<small>JUL</small></div>
    <h3>LOREM IPSUM DOLOR SIT AMET</h3>
    <p>Partner challenge day with team relays, core finishers and a healthy lunch after.</p>
    <span class="btn">Read More</span>
  </div>
</section>

<section class="testimonials">
  <h2 class="heading">Client <strong>Testimonials</strong><div class="rule"></div></h2>
  <svg class="arrow" style="left:22px" viewBox="0 0 30 50"><path d="M24 4L6 25l18 21" fill="none" stroke="#fff" stroke-width="4"/></svg>
  <svg class="arrow" style="right:22px" viewBox="0 0 30 50"><path d="M6 4l18 21L6 46" fill="none" stroke="#fff" stroke-width="4"/></svg>
  <div class="quote">
    <span class="quote-mark">“</span>
    I joined the outdoor bootcamp to get back in shape after a long winter and stayed for the people. Each session is different, the coaching is patient and clear, and I always leave feeling stronger than when I arrived. Within three months I had more energy at work, slept better and finally ran my first ten kilometre race without stopping. I recommend it to anyone who wants honest training that actually fits a busy life.
  </div>
  <div class="author">DANA KORRICK</div>
</section>

<footer class="site-footer">
  <div class="newsletter">
    <span class="label">NEWSLETTER SIGNUP</span>
    <span class="field" style="width:380px;height:38px">Enter your email here</span>
    <span class="subscribe">SUBSCRIBE</span>
    <span class="follow"><span class="label">FOLLOW US</span><span class="dot" style="background:#fff"></span><span class="dot" style="background:#9a9a9a"></span></span>
  </div>
  <div class="footer-rule"></div>

  <div class="col inquiry">
    <h4><span></span>QUICK INQUIRY</h4>
    <span class="field" style="left:0;top:48px">Name</span>
    <span class="field" style="left:0;top:96px">Email Address</span>
    <span class="field" style="left:0;top:144px">Phone Number</span>
    <span class="field" style="left:240px;top:48px;width:240px;height:94px;align-items:flex-start;padding-top:8px">Message</span>
    <span class="subscribe" style="position:absolute;left:240px;top:150px;width:240px;height:30px">SUBMIT</span>
  </div>

  <div class="col links" style="left:640px">
    <h4><span></span>QUICK LINKS</h4>
    <ul><li>Home</li><li>About</li><li>Services</li><li>Blog</li><li>Videos</li><li>Programs</li><li>Contact</li></ul>
  </div>

  <div class="col details" style="left:900px">
    <h4><span></span>CONTACT DETAILS</h4>
    <p><span class="dot" style="width:22px;height:22px;background:#fff"></span>206-555-0172</p>
    <p><span class="dot" style="width:22px;height:22px;background:#fff"></span>info@vorelan.com</p>
    <p><span class="brand-mark" style="background:#fff;width:20px;height:20px"></span><span class="brand-name">VORELAN</span></p>
  </div>

  <div class="copyright">COPYRIGHT 2016 VORELAN | ALL RIGHT RESERVED</div>
</footer>

</body>
</html>
```